A5 Patient Information Booklet (Chiropractic Clinic) 4-8 pages

Here’s a polished, professional rewrite of your full brief and content, with clearer structure, corrected language, and a premium tone:

---

**Project Title:** Premium Patient Information Brochure (Chiropractic & Wellness Clinic)

---

### **Overview**

We are a health and wellness clinic seeking a premium, high-end patient information brochure to provide following a patient’s initial consultation and first treatment.

The purpose of this booklet is to:

* Reinforce trust and professionalism
* Help patients understand what to expect next
* Encourage adherence to care recommendations
* Position the clinic as calm, expert-led, and results-driven

---

### **Format**

* 4–8 page booklet (A5 or similar size)
* Print-ready and digital versions required

---

### **Target Audience**

Patients who have just completed their initial consultation and may have begun treatment. They may already be experiencing physical or mental changes, so the brochure should guide, reassure, and educate them on what comes next.

---

### **Tone & Style**

* Premium, calm, and reassuring
* Modern wellness aesthetic (not overly clinical)
* Clean layout with minimal clutter
* Soft, neutral colour palette (whites, creams, muted greens, soft blues)
* Elegant typography (e.g. Montserrat / Lato)
* High-end, trustworthy, and professional feel

---

### **Key Messages**

#### 1. Listen to Your Body

Patients may feel different after treatment. Reassure them that this is normal and part of the healing process.

#### 2. Post-Treatment Advice

* Stay well hydrated
* Rest if needed
* Avoid overexertion if the body requires recovery

#### 3. Healing is a Journey (Core Concept)

A strong visual metaphor of a **“road to recovery”** or **journey** should be central to the design.

This journey should clearly illustrate three phases:

* **Phase 1: Initial Care (Weeks 1–6)**
Focus: Reducing pain/discomfort, calming the body, and initiating response to treatment

* **Phase 2: Corrective Care (Weeks 6–12)**
Focus: Addressing underlying issues, improving function, and creating lasting change

* **Phase 3: Wellness / Maintenance (Ongoing)**
Focus: Maintaining progress, preventing relapse, and supporting long-term wellbeing

**Important:**

* Emphasise that this is not a quick fix
* Progress requires time and consistency
* Each patient follows an individualised care plan
* The journey should feel structured, positive, and achievable

#### 4. Personalised Care

Reinforce that every treatment plan is tailored specifically to the individual.

#### 5. Professional Reassurance

Patients should feel confident they are in expert hands and supported throughout their journey.

---

### **Design Direction**

* Use imagery that reflects calmness, progression, and wellness (e.g. pathways, nature, soft gradients)
* Avoid generic stock imagery
* **Only use original clinic images from website and social media**
* Prioritise white space and clarity
* Aim for a luxury spa/medical hybrid aesthetic

---

## **Content Structure (Page-by-Page)**

### **Front Cover**

* Clean, minimal, premium design
* Clinic branding

---

### **Page 1: Patient Case Summary**

**Title:** *Welcome to Fernwell Spine Studio*

Thank you for choosing Fernwell Spine Studio.

This booklet is designed to guide you through:

* What we found during your initial consultation
* Your personalised recommended treatment plan
* Your road to recovery
* Long-term wellness care
* Why we take the approach we do

---

### **Page 2: Your Care Journey**

**Stage 1: Your Initial Consultation**

Today we completed a comprehensive assessment of your health and function, including:

* Full case history and discussion of your symptoms and goals
* Orthopaedic and neurological testing
* Postural and movement assessment
* Initial treatment (where appropriate)

**What this tells us:**

* How your body is currently functioning
* Where areas of stress or dysfunction may be present
* The most appropriate and effective path forward for your care

---

### **Page 3: Your Suggested Treatment Plan**

Based on today’s findings, your recommended care plan is:

**______ treatments over ______ weeks**

This should be viewed alongside your *Road to Recovery* to help you understand what to expect.

We have also discussed:

* Expected timelines for improvement
* Available payment options

**After Treatment:**
It is common to feel different following treatment. This is a normal response as your body begins to adapt and respond.

We recommend:

* Staying well hydrated
* Allowing time for rest and recovery
* Avoiding overexertion if your body feels it needs it

---

### **Page 4: What to Expect Next**

Healing is not always linear—it is a process that occurs over time.

Your care will typically progress through the following stages:

* **Relief Care**
Focused on reducing discomfort and calming the body

* **Corrective Care**
Focused on addressing underlying issues and improving function
(This phase may include prescribed exercises)

* **Maintenance / Wellness Care**
Focused on sustaining progress, preventing recurrence, and supporting long-term health

---

### **Page 5: Understanding Chiropractic Care**

**What is Chiropractic?**
Chiropractic care focuses on the relationship between the spine, nervous system, and overall body function.

By improving spinal movement and alignment, chiropractic care helps support the nervous system, allowing the body to function and heal more effectively.

**About Fernwell Spine Studio**
At Fernwell Spine Studio, our approach is centred around personalised, patient-focused care. We aim to not only relieve symptoms but to address underlying causes and support long-term wellbeing.

---

### **Back Page**

* Clinic contact details
* Website
* Social media icons/handles

**Closing Message:**
“A healthier, stronger you—supported every step of the way.”

---

### **Deliverables**

* Print-ready PDF
* Editable source files

---

### **Additional Notes**

* The brochure should feel valuable and worth keeping
* Encourage long-term care in a subtle, non-pushy way
* Maintain clarity, readability, and strong visual hierarchy
* Balance professionalism with warmth and approachability

---

If you’d like, I can also turn this into **actual brochure copy (fully written, patient-facing text)** or help you refine it further for a designer.

Existing patients who want to feel better and look after themselves that is given after their initil consultation appointment

Chiropractic, wellness, health

• Montserrat or Lato

0094D4
00A9DD
6FCCEA
C7EBF8
E9F6FB
00AB8E
00BBA5
67D7C9
C6EFE9
E9F9F6
6B429C
8869AF
B7A5CE
E3DAEB
F3F0F8

• my own photos, look premium wellness, be clear and simple to understand for patients journey or what to expect next and over time
• USe my social media/website for ideas
• generic photos and images

```html
<!DOCTYPE html>
<html lang="en">
<head>
<meta charset="utf-8">
<title>Fernwell Spine Studio – Patient Information Booklet</title>
<link href="https://fonts.googleapis.com/css2?family=Montserrat:wght@400;500;600;700;800;900&display=swap" rel="stylesheet">
<style>
:root{
  --teal:#13a89e;
  --teal-dark:#0e8f86;
  --ink:#1f1f1f;
  --muted:#3a3a3a;
  --pink:#f984c5;
  --lilac:#b39bd9;
  --blue:#6bb5e8;
  --stage:#676767;
  --pill:#3b2b2b;
}
*{box-sizing:border-box;margin:0;padding:0}
html,body{width:1200px;height:2879px;overflow:hidden}
body{background:var(--stage);font-family:"Montserrat",Arial,sans-serif;color:var(--ink);position:relative}

/* ---------- cover spread ---------- */
.spread{position:absolute;left:103px;top:61px;width:981px;height:694px;background:#fff;overflow:hidden}
.spread-art{position:absolute;inset:0}
.closing{position:absolute;left:41px;top:424px;width:220px}
.closing h3{color:var(--teal);font-size:16px;font-weight:800;letter-spacing:.2px}
.closing p{font-size:16px;font-weight:700;line-height:1.25;margin-top:2px}
.mark{position:absolute;text-align:center}
.mark .disc{display:block;margin:0 auto 8px;border-radius:50%;border:5px solid var(--teal)}
.mark .name{color:var(--teal);font-weight:700;letter-spacing:.5px;line-height:1.15}
.mark-back{left:275px;top:360px;width:180px}
.mark-back .disc{width:82px;height:82px}
.mark-back .name{font-size:16px}
.mark-cover{left:765px;top:40px;width:180px}
.mark-cover .disc{width:82px;height:82px}
.mark-cover .name{font-size:17px}
.contact{position:absolute;left:41px;top:541px;width:230px}
.contact .c-name{font-size:15px;font-weight:700;letter-spacing:.3px}
.contact .c-sub{font-size:13px;color:var(--teal);font-weight:500;margin-bottom:8px}
.contact li{list-style:none;font-size:12px;display:flex;align-items:center;gap:6px;height:20px}
.contact .ic{width:11px;height:11px;border-radius:50%;background:var(--teal);flex:none}
.contact .sq{width:13px;height:13px;border-radius:2px;flex:none}
.map{position:absolute;left:274px;top:546px;width:173px;height:108px;border:2px solid var(--teal);border-radius:10px;background:linear-gradient(135deg,#eef8f7,#dcefee)}
.cover-copy{position:absolute;right:43px;top:503px;width:430px;text-align:right}
.cover-copy h1{font-size:21.5px;font-weight:800;line-height:1.2;letter-spacing:.2px}
.cover-copy p{font-size:13px;line-height:1.17;margin-top:6px;color:#1d1d1d}
.pill{position:absolute;right:43px;top:633px;width:310px;height:29px;border-radius:15px;background:var(--pill);color:#fff;font-size:16.5px;font-weight:500;display:flex;align-items:center;justify-content:center}

/* ---------- booklet pages ---------- */
.page{position:absolute;width:459px;height:651px;background:linear-gradient(180deg,var(--pink) 0%,var(--lilac) 50%,var(--blue) 100%);padding:26px}
.card{width:100%;height:100%;background:#fff;border-radius:12px;padding:24px 24px 26px;display:flex;flex-direction:column}
.p1{left:103px;top:800px}.p2{left:625px;top:800px}
.p3{left:103px;top:1487px}.p4{left:625px;top:1487px}
.p5{left:103px;top:2170px}.p6{left:625px;top:2170px}
.photo{width:100%;margin-top:auto;border-radius:2px;flex:none}
.h-big{color:var(--teal);font-size:25px;font-weight:800;line-height:1.18;letter-spacing:.3px}
.h-mid{color:var(--teal);font-size:20px;font-weight:800;letter-spacing:.3px}
.h-title{color:var(--teal);font-size:18px;font-weight:700}
.lead{font-size:20px;font-weight:700;line-height:1.3;margin-top:16px}
.sub{color:var(--teal);font-weight:700;font-size:14.5px;margin-top:20px}
.ticks{margin-top:6px}
.ticks li{list-style:none;position:relative;padding-left:16px;font-size:13px;line-height:1.3;margin-bottom:10px}
.ticks li::before{content:"";position:absolute;left:0;top:4px;width:10px;height:10px;border-radius:50%;background:var(--teal)}
.ticks li::after{content:"";position:absolute;left:3.6px;top:5.5px;width:2.5px;height:4.5px;border:solid #fff;border-width:0 1.5px 1.5px 0;transform:rotate(45deg)}
.ticks.tight li{margin-bottom:4px}
.ticks.two{display:grid;grid-template-columns:1fr 1fr;column-gap:8px}
.ticks.two li{font-size:12px;margin-bottom:2px}
.body-t{font-size:13px;line-height:1.28;color:var(--muted)}
.just{text-align:justify}
.stage-h{font-size:16px;font-weight:700;line-height:1.2;margin-top:6px}
.blank{display:inline-block;width:115px;border-bottom:1px solid #333}
.blank.s{width:62px}
.steps{margin-top:14px}
.step{display:flex;gap:12px;margin-bottom:12px}
.step .ring{width:47px;height:47px;border-radius:50%;background:var(--teal);flex:none;box-shadow:inset 0 0 0 3px var(--teal),inset 0 0 0 5px #fff}
.step h4{color:var(--teal);font-size:13px;font-weight:700}
.step p{font-size:13px;line-height:1.22;color:var(--muted)}

/* key messages */
.p6 .card{position:relative;display:block}
.km-left{position:absolute;left:24px;top:22px;width:176px}
.km-right{position:absolute;left:219px;top:22px;width:164px}
.km-title{font-size:19px;font-weight:800;letter-spacing:.2px;text-decoration:underline;text-underline-offset:2px}
.km h5{display:flex;align-items:flex-start;gap:5px;color:var(--teal);font-size:12.5px;font-weight:600;margin-top:10px;line-height:1.15}
.km h5 u{text-underline-offset:2px}
.km .n{background:#222;color:#fff;font-size:10px;font-weight:700;width:13px;height:13px;display:inline-flex;align-items:center;justify-content:center;flex:none;margin-top:1px}
.km p,.km li{font-size:9.5px;line-height:1.2;color:#333}
.km p{margin-top:3px}
.km .ph{margin-top:6px;font-size:9.5px;line-height:1.2}
.km .ph b{font-weight:700;color:#222}
.km .ph .f{color:var(--teal);font-weight:700}
.km .ticks li{font-size:9.5px;padding-left:12px;margin-bottom:1px}
.km .ticks li::before{width:7px;height:7px;top:3px}
.km .ticks li::after{left:2.4px;top:3.8px;width:1.8px;height:3.2px;border-width:0 1px 1px 0}
.km .imp{color:var(--teal);font-size:11.5px;font-weight:700;margin-top:8px;text-decoration:underline}
.km .imp-list{width:130px}
.km .imp-list li{margin-bottom:6px}
.road{position:absolute;right:24px;bottom:26px;width:219px;height:154px;border:3px solid #2c2c2c;background:linear-gradient(180deg,#f3f6fb 0%,#e8eef6 45%,#fbe7d4 100%)}
</style>
</head>
<body>

<!-- ================= Cover spread: back page + front cover ================= -->
<section class="spread">
  <svg class="spread-art" width="981" height="694" viewBox="0 0 981 694" aria-hidden="false">
    <defs>
      <linearGradient id="tealPhoto" x1="0" y1="0" x2="1" y2="1">
        <stop offset="0" stop-color="#2bb3a8"/><stop offset="1" stop-color="#0e8c84"/>
      </linearGradient>
      <linearGradient id="coverBand" x1="0" y1="0" x2="0" y2="1">
        <stop offset="0" stop-color="#ee84c4"/><stop offset="1" stop-color="#a3a6e4"/>
      </linearGradient>
      <linearGradient id="roomPhoto" x1="0" y1="0" x2="1" y2="1">
        <stop offset="0" stop-color="#e6ded4"/><stop offset=".6" stop-color="#b9ab9f"/><stop offset="1" stop-color="#6e6560"/>
      </linearGradient>
      <linearGradient id="smallPhoto" x1="0" y1="0" x2="0" y2="1">
        <stop offset="0" stop-color="#d8cfc6"/><stop offset="1" stop-color="#a08f82"/>
      </linearGradient>
      <linearGradient id="portrait" x1="0" y1="0" x2="0" y2="1">
        <stop offset="0" stop-color="#cdbba8"/><stop offset="1" stop-color="#8e7868"/>
      </linearGradient>
    </defs>
    <path role="img" aria-label="Teal-toned photo of a treatment couch and linen" d="M0,0 H500 V230 C400,255 280,300 0,345 Z" fill="url(#tealPhoto)"/>
    <path d="M470,694 V430 C600,480 800,470 981,280 V694 Z" fill="url(#coverBand)"/>
    <circle role="img" aria-label="Photo of the chiropractor treating a patient in a bright clinic room" cx="690" cy="215" r="280" fill="url(#roomPhoto)" stroke="#fff" stroke-width="8"/>
    <circle cx="860" cy="105" r="132" fill="#fff"/>
    <circle role="img" aria-label="Photo of the chiropractor treating a patient's neck" cx="162" cy="263" r="115" fill="url(#smallPhoto)" stroke="#fff" stroke-width="6"/>
    <circle role="img" aria-label="Portrait photo of the lead chiropractor" cx="553" cy="441" r="92" fill="url(#portrait)" stroke="#fff" stroke-width="6"/>
  </svg>

  <div class="closing">
    <h3>CLOSING MESSAGE:</h3>
    <p>A healthier, stronger you — supported every step of the way.</p>
  </div>

  <div class="mark mark-back"><span class="disc"></span><span class="name">FERNWELL SPINE STUDIO</span></div>

  <div class="contact">
    <div class="c-name">FERNWELL SPINE STUDIO</div>
    <div class="c-sub">Chiropractic &amp; Wellness</div>
    <ul>
      <li><span class="ic"></span>12 Linden Row, Ashcombe AC4 7QT</li>
      <li><span class="ic"></span>info@fernwellspinestudio.com</li>
      <li><span class="ic"></span>www.fernwellspinestudio.com</li>
      <li><span class="sq" style="background:#3b5bb5"></span><span class="sq" style="background:#d9457f"></span>@fernwellspine_studio</li>
    </ul>
  </div>
  <div class="map" role="img" aria-label="Street map showing the clinic location"></div>

  <div class="mark mark-cover"><span class="disc"></span><span class="name">FERNWELL SPINE STUDIO</span></div>

  <div class="cover-copy">
    <h1>ALIGN YOUR BODY,<br>ELEVATE YOUR WELLBEING</h1>
    <p>At Fernwell Spine Studio Chiropractic and Wellness Ashcombe, we offer personalised chiropractic care for adults &amp; families who want to feel their best — whether that’s easing discomfort, improving movement, or supporting long-term wellbeing.</p>
  </div>
  <div class="pill">www.fernwellspinestudio.com</div>
</section>

<!-- ================= Page 1 ================= -->
<section class="page p1"><div class="card">
  <h2 class="h-big">WELCOME TO<br>FERNWELL SPINE STUDIO</h2>
  <p class="lead">Thank you for choosing Fernwell Spine Studio.</p>
  <h3 class="sub">This booklet is designed to guide you through:</h3>
  <ul class="ticks" style="margin-top:8px">
    <li>What we found during your initial consultation</li>
    <li>Your personalised recommended treatment plan</li>
    <li>Your road to recovery</li>
    <li>Long-term wellness care</li>
    <li>Why we take the approach we do</li>
  </ul>
  <div class="photo" role="img" aria-label="Photo of the clinic treatment room with adjusting tables" style="height:228px;background:linear-gradient(135deg,#d9d4cc,#a8a29b 60%,#7b7771)"></div>
</div></section>

<!-- ================= Page 2 ================= -->
<section class="page p2"><div class="card">
  <h2 class="h-mid">YOUR CARE JOURNEY</h2>
  <p class="stage-h">Stage 1:<br>Your Initial Consultation</p>
  <p class="sub" style="margin-top:10px;font-size:13.5px;font-weight:600;line-height:1.22">Today we completed a comprehensive assessment of your health and function, including:</p>
  <ul class="ticks tight" style="margin-top:8px">
    <li>Full case history &amp; discussion of your symptoms &amp; goals</li>
    <li>Orthopaedic and neurological testing</li>
    <li>Postural and movement assessment</li>
    <li>Initial treatment (where appropriate)</li>
  </ul>
  <h3 class="sub" style="margin-top:16px">WHAT THIS TELLS US:</h3>
  <ul class="ticks" style="margin-top:4px">
    <li>How your body is currently functioning</li>
    <li>Where areas of stress or dysfunction may be present</li>
    <li>The most appropriate and effective path forward for your care</li>
  </ul>
  <div class="photo" role="img" aria-label="Photo of the chiropractor assessing a patient by a large window" style="height:208px;background:linear-gradient(135deg,#e8e4de,#b3aca4 55%,#6e6a66)"></div>
</div></section>

<!-- ================= Page 3 ================= -->
<section class="page p3"><div class="card">
  <h2 class="h-title">Your Suggested Treatment Plan</h2>
  <p class="body-t" style="font-size:12.5px;margin-top:4px;color:#222">Based on today’s findings, your recommended care plan is:</p>
  <p class="body-t" style="font-size:12.5px;margin-top:12px;color:#222"><span class="blank"></span> treatments over<span class="blank s"></span> weeks</p>
  <p style="font-size:12.5px;font-weight:600;line-height:1.25;margin-top:18px">This should be viewed alongside your *Road to Recovery* to help you understand what to expect.</p>
  <h3 class="sub" style="margin-top:12px">We have also discussed:</h3>
  <ul class="ticks two" style="margin-top:2px">
    <li>Expected timelines for improvement</li>
    <li>Available payment options</li>
  </ul>
  <h3 class="sub" style="margin-top:10px">After Treatment:</h3>
  <p class="body-t just" style="font-size:12.5px">It is common to feel different following treatment. This is a normal response as your body begins to adapt and respond.</p>
  <h3 class="sub" style="margin-top:12px">We recommend:</h3>
  <ul class="ticks two" style="margin-top:2px">
    <li>Staying well hydrated</li>
    <li>Allowing time for rest &amp; recovery</li>
    <li style="grid-column:1 / 3">Avoiding overexertion if your body feels it needs it</li>
  </ul>
  <div class="photo" role="img" aria-label="Black and white photo of the chiropractor working on a patient's back" style="height:246px;background:linear-gradient(135deg,#d2d2d2,#8a8a8a 60%,#3c3c3c)"></div>
</div></section>

<!-- ================= Page 4 ================= -->
<section class="page p4"><div class="card">
  <h2 class="h-title">What to Expect Next</h2>
  <p class="body-t" style="font-size:13px;margin-top:2px">Healing is not always linear—it is a process that occurs over time.</p>
  <p style="font-size:13px;font-weight:600;line-height:1.25;margin-top:14px">Your care will typically progress through the following stages:</p>
  <div class="steps">
    <div class="step"><span class="ring"></span><div><h4>Relief Care</h4><p>Focused on reducing discomfort and calming the body</p></div></div>
    <div class="step"><span class="ring"></span><div><h4>Corrective Care</h4><p>Focused on addressing underlying issues and improving function (This phase may include prescribed exercises)</p></div></div>
    <div class="step"><span class="ring"></span><div><h4>Maintenance / Wellness Care</h4><p>Focused on sustaining progress, preventing recurrence, and supporting long-term health</p></div></div>
  </div>
  <div class="photo" role="img" aria-label="Photo of the chiropractor adjusting a patient's neck in a sunlit room" style="height:252px;background:linear-gradient(135deg,#e6e1d9,#b6ab9e 55%,#6f8a63)"></div>
</div></section>

<!-- ================= Page 5 ================= -->
<section class="page p5"><div class="card">
  <h2 style="font-size:18px;font-weight:700;margin-top:4px">Understanding Chiropractic Care</h2>
  <h3 class="sub" style="margin-top:2px">What is Chiropractic?</h3>
  <p class="body-t just">Chiropractic care focuses on the relationship between the spine, nervous system, and overall body function.</p>
  <p class="body-t just" style="margin-top:14px">By improving spinal movement and alignment, chiropractic care helps support the nervous system, allowing the body to function and heal more effectively.</p>
  <h3 class="sub" style="margin-top:20px">About Fernwell Spine Studio</h3>
  <p class="body-t just">At Fernwell Spine Studio, our approach is centred around personalised, patient-focused care. We aim to not only relieve symptoms but to address underlying causes and support long-term wellbeing.</p>
  <div class="photo" role="img" aria-label="Photo of a calm treatment room with an adjusting table and wooden floor" style="height:293px;background:linear-gradient(180deg,#e9e6df,#cfc7bb 55%,#8f7a63)"></div>
</div></section>

<!-- ================= Page 6 ================= -->
<section class="page p6"><div class="card km">
  <div class="km-left">
    <h2 class="km-title">KEY MESSAGES:</h2>
    <h5><span class="n">1</span><u>Listen to Your Body</u></h5>
    <p>Patients may feel different after treatment. Reassure them that this is normal &amp; part of the healing process.</p>
    <h5><span class="n">2</span><u>Post-Treatment Advice</u></h5>
    <ul class="ticks" style="margin-top:3px">
      <li>Stay well hydrated</li>
      <li>Rest if needed</li>
      <li>Avoid overexertion if the body requires recovery</li>
    </ul>
    <h5><span class="n">3</span><u>Healing is a Journey (Core Concept)</u></h5>
    <div class="ph"><span class="f">PHASE 1:</span><br><b>Initial Care (Weeks 1–6)</b><br><span class="f">Focus:</span> Reducing pain/discomfort, calming the body and helping you begin to respond to treatment.</div>
    <div class="ph"><span class="f">PHASE 2:</span><br><b>Corrective Care (Weeks 6–12)</b><br><span class="f">Focus:</span> Addressing underlying issues, improving function, and creating lasting change</div>
    <div class="ph"><span class="f">PHASE 3:</span><br><b>Wellness / Maintenance (Ongoing)</b><br><span class="f">Focus:</span> Maintaining progress, preventing relapse, and supporting long-term health and wellbeing.</div>
    <div class="imp">IMPORTANT:</div>
    <ul class="ticks imp-list" style="margin-top:3px">
      <li>Emphasise that this is not a quick fix</li>
      <li>Progress requires time and consistency</li>
      <li>Each patient follows an individualised care plan</li>
      <li>The journey should feel structured, positive and achievable</li>
    </ul>
  </div>
  <div class="km-right">
    <div role="img" aria-label="Photo of the chiropractor treating a patient lying on an adjusting table" style="height:233px;background:linear-gradient(180deg,#ece9e4,#c4bcb2 55%,#7d8fb3)"></div>
    <h5><span class="n">4</span>Personalised Care</h5>
    <p>Reinforce that every treatment plan is tailored specifically to the individual.</p>
    <h5><span class="n">5</span>Professional Reassurance</h5>
    <p>Patients should feel confident they are in expert hands and supported throughout their journey.</p>
  </div>
  <div class="road" role="img" aria-label="Road to recovery chart showing a winding path rising through relief, corrective and wellness phases over time"></div>
</div></section>

</body>
</html>
```